Letterhead, stationery and email signature for construction business

I need the letterhead, stationery and email signature designs for a construction business. I want them to have a corporate feel to them.

I've attached the logo for reference.

```html
<!DOCTYPE html>
<html lang="en">
<head>
<meta charset="utf-8">
<title>Torvane Builds Stationery</title>
<link href="https://fonts.googleapis.com/css2?family=Lato:wght@400;700;900&family=Open+Sans:wght@400;600;700&family=Pinyon+Script&display=swap" rel="stylesheet">
<style>
  :root {
    --brand-blue: #2f55a4;
    --ink: #1a1a1a;
    --header-black: #151515;
    --text: #222222;
    --muted: #444444;
    --paper: #ffffff;
    --canvas: #ffffff;
    --photo-tone: #d9d6d2;
    --watermark: #eef0f8;
  }
  * { box-sizing: border-box; margin: 0; padding: 0; }
  html, body { width: 1200px; height: 807px; overflow: hidden; background: var(--canvas); }
  body { position: relative; font-family: "Lato", sans-serif; color: var(--text); }

  .sheet {
    position: absolute;
    background: var(--paper);
    box-shadow: 4px 8px 14px rgba(0,0,0,0.28);
    overflow: hidden;
  }

  .brand-name {
    font-family: "Lato", sans-serif;
    font-weight: 900;
    color: var(--brand-blue);
    letter-spacing: 0.3px;
    white-space: nowrap;
    display: flex;
    align-items: center;
    gap: 6px;
  }
  .brand-mark { display: inline-block; flex: none; background: var(--brand-blue); }

  /* Letterhead */
  .letterhead { left: 136px; top: 97px; width: 431px; height: 609px; }
  .letterhead-header { position: absolute; left: 0; top: 0; width: 431px; height: 130px; }
  .letterhead .brand-name { position: absolute; left: 21px; top: 33px; font-size: 17px; }
  .letterhead .brand-mark { width: 17px; height: 17px; }
  .contact-block { position: absolute; font-size: 8.2px; line-height: 9.5px; color: var(--muted); }
  .letterhead .contact-block { left: 309px; top: 58px; }
  .contact-block .gap { height: 9px; }
  .contact-line { display: flex; align-items: center; gap: 4px; }
  .contact-line svg { width: 7px; height: 7px; flex: none; }

  .letter-body { position: absolute; left: 21px; top: 157px; width: 390px; font-size: 8.6px; line-height: 9.8px; color: var(--text); }
  .letter-body p { margin-bottom: 10px; text-align: justify; }
  .letter-body .left { text-align: left; }
  .letter-body .salutation { font-size: 10.5px; font-weight: 700; margin-bottom: 11px; }
  .letter-body .sign-off { margin-top: 14px; margin-bottom: 38px; }
  .signature { font-family: "Pinyon Script", cursive; font-size: 20px; color: var(--ink); }

  /* Email signature */
  .email-signature { left: 620px; top: 69px; width: 475px; height: 148px; font-family: "Open Sans", sans-serif; }
  .portrait { position: absolute; left: 21px; top: 24px; width: 99px; height: 99px; border-radius: 50%; border: 1.5px solid var(--brand-blue); background: radial-gradient(circle at 50% 45%, #efe6dc 0%, var(--photo-tone) 60%, #bfb8b0 100%); }
  .person { position: absolute; left: 165px; top: 18px; }
  .person-name { font-weight: 700; font-size: 12px; color: var(--brand-blue); }
  .person-role { font-size: 8px; color: var(--muted); margin-top: -1px; }
  .rule { width: 38px; height: 1px; background: var(--brand-blue); margin: 7px 0; }
  .person .addr { font-size: 8px; line-height: 11px; color: var(--muted); }
  .person .contact-line { font-size: 8px; line-height: 11px; color: var(--ink); }
  .email-signature .brand-name { position: absolute; right: 20px; top: 32px; font-family: "Lato", sans-serif; font-size: 15px; }
  .email-signature .brand-mark { width: 15px; height: 15px; }
  .social { position: absolute; left: 402px; top: 116px; display: flex; gap: 3px; }
  .social span { width: 11px; height: 11px; border-radius: 50%; background: var(--brand-blue); display: block; }

  /* Envelope back */
  .envelope-back { left: 620px; top: 269px; width: 439px; height: 194px; }
  .envelope-back svg { position: absolute; left: 0; top: 0; }
  .flap-mark { position: absolute; left: 209px; top: 14px; width: 20px; height: 20px; background: var(--paper); }

  /* Envelope front */
  .envelope-front { left: 620px; top: 516px; width: 439px; height: 190px; }
  .envelope-front .brand-name { position: absolute; left: 13px; top: 26px; font-size: 14px; }
  .envelope-front .brand-mark { width: 14px; height: 14px; }
  .envelope-front .contact-block { left: 13px; top: 153px; font-size: 8.4px; line-height: 11px; }
  .watermark-panel { position: absolute; left: 281px; top: 0; width: 158px; height: 174px; background: linear-gradient(135deg, #f1f1f3 0%, var(--watermark) 100%); }
</style>
</head>
<body>

<section class="sheet letterhead">
  <svg class="letterhead-header" viewBox="0 0 431 130" aria-hidden="true">
    <path d="M0,0 H431 V34 C380,18 330,22 260,52 C180,86 90,100 0,92 Z" fill="var(--header-black)"/>
    <path d="M0,104 C90,118 170,102 250,76 C330,48 380,22 431,44" fill="none" stroke="var(--brand-blue)" stroke-width="5"/>
    <path d="M50,104 C130,98 200,80 270,58 C320,42 360,30 400,28" fill="none" stroke="var(--brand-blue)" stroke-width="1.5"/>
    <path d="M260,52 C330,20 390,14 431,34 V40 C390,22 340,26 270,56 Z" fill="var(--brand-blue)"/>
  </svg>
  <div class="brand-name"><span class="brand-mark"></span>TORVANE BUILDS</div>
  <div class="contact-block">
    <div>Your address, City</div>
    <div>State, Zip 1234</div>
    <div class="gap"></div>
    <div class="contact-line"><svg viewBox="0 0 10 10"><path d="M1,4 Q5,0 9,4 L8,5 L6,4 L6,3 L4,3 L4,4 L2,5 Z M2,6 H8 V9 H2 Z" fill="var(--brand-blue)"/></svg>123 456 789</div>
    <div class="contact-line"><svg viewBox="0 0 10 10"><rect x="0.5" y="2" width="9" height="6" fill="var(--brand-blue)"/><path d="M0.5,2 L5,5.5 L9.5,2" fill="none" stroke="#fff" stroke-width="0.8"/></svg>info@yourgmail.com</div>
    <div class="contact-line"><svg viewBox="0 0 10 10"><circle cx="5" cy="5" r="4.5" fill="var(--brand-blue)"/></svg>www.yourwebsite.com</div>
  </div>
  <div class="letter-body">
    <p class="left">January-03-2020</p>
    <p class="left">Mr, Peter Hale<br>President</p>
    <p class="left">Northfield Corporation<br>123 Street Name, Suite# 10<br>City, State, 120023</p>
    <p class="salutation left">Dear Mr, Peter</p>
    <p>Lorem ipsum dolor sit amet, consectetur adipiscing elit, sed do eiusmod tempor incididunt ut labore et dolore magna aliqua. Ut enim ad minim veniam, quis nostrud exercitation ullamco laboris nisi ut aliquip ex ea commodo consequat. Duis aute irure dolor in reprehenderit in voluptate velit esse cillum dolore eu fugiat nulla pariatur.</p>
    <p>Lorem ipsum dolor sit amet, consectetur adipiscing elit, sed do eiusmod tempor incididunt ut labore et dolore magna aliqua. Ut enim ad minim veniam, quis nostrud exercitation ullamco laboris nisi ut aliquip ex ea commodo consequat. Duis aute irure dolor in reprehenderit in voluptate velit esse cillum dolore eu fugiat nulla pariatur.</p>
    <p>Lorem ipsum dolor sit amet, consectetur adipiscing elit, sed do eiusmod tempor incididunt ut labore et dolore magna aliqua. Ut enim ad minim veniam, quis nostrud exercitation ullamco laboris nisi ut aliquip ex ea commodo consequat.</p>
    <p>Excepteur sint occaecat cupidatat non proident, sunt in culpa qui officia deserunt mollit anim id est laborum. re et dolore magnam aliquam quaerat voluptatem.</p>
    <p class="left sign-off">Regards</p>
    <div class="signature">Laura Bennett</div>
  </div>
</section>

<section class="sheet email-signature">
  <div class="portrait" role="img" aria-label="Portrait photo of the team member"></div>
  <div class="person">
    <div class="person-name">DANIEL REYES</div>
    <div class="person-role">Managing Director</div>
    <div class="rule"></div>
    <div class="addr">Your address, City<br>State, Zip 1234</div>
    <div class="rule"></div>
    <div class="contact-line"><svg viewBox="0 0 10 10"><path d="M1,4 Q5,0 9,4 L8,5 L6,4 L6,3 L4,3 L4,4 L2,5 Z M2,6 H8 V9 H2 Z" fill="var(--brand-blue)"/></svg>123-456-789</div>
    <div class="contact-line"><svg viewBox="0 0 10 10"><rect x="0.5" y="2" width="9" height="6" fill="var(--brand-blue)"/><path d="M0.5,2 L5,5.5 L9.5,2" fill="none" stroke="#fff" stroke-width="0.8"/></svg>info@mailbox.com</div>
    <div class="contact-line"><svg viewBox="0 0 10 10"><circle cx="5" cy="5" r="4.5" fill="var(--brand-blue)"/></svg>www.yourwebsite.com</div>
  </div>
  <div class="brand-name"><span class="brand-mark"></span>TORVANE BUILDS</div>
  <div class="social"><span></span><span></span><span></span><span></span></div>
</section>

<section class="sheet envelope-back">
  <svg width="439" height="194" viewBox="0 0 439 194" aria-hidden="true">
    <path d="M0,0 H439 C432,30 420,36 405,38 L220,60 L35,38 C18,36 6,25 0,0 Z" fill="var(--brand-blue)"/>
  </svg>
  <span class="flap-mark"></span>
</section>

<section class="sheet envelope-front">
  <div class="watermark-panel"></div>
  <div class="brand-name"><span class="brand-mark"></span>TORVANE BUILDS</div>
  <div class="contact-block">
    <div>Your address, City</div>
    <div>State, Zip 1234</div>
  </div>
</section>

</body>
</html>
```